Website update for Harborline Ledger Partners & Bookkeeping

Our website needs updating
www.harborlineledgerpartners.com
Here are some of our latest print pieces to use as a guide?
I have also attached our graphic identity guide which includes the Pantone colors

Target Market(s)

Insurance Agencies

Industry/Entity Type

Accounting

Number of Pages Required

5+ page

```html
<!DOCTYPE html>
<html lang="en">
<head>
<meta charset="utf-8">
<title>Harborline Ledger Partners &amp; Bookkeeping</title>
<link href="https://fonts.googleapis.com/css2?family=Open+Sans:wght@400;600;700&family=Raleway:wght@500;700&display=swap" rel="stylesheet">
<style>
:root{
  --teal:#1fb29c;
  --teal-dark:#16907e;
  --teal-light:#dff3ef;
  --ink:#2f3538;
  --nav:#3d4245;
  --muted:#7a8285;
  --line:#d9dfe0;
  --white:#ffffff;
  --band:#34393c;
  --footer:#118472;
}
*{box-sizing:border-box;margin:0;padding:0}
html,body{width:1200px;height:2304px;overflow:hidden}
body{font-family:"Open Sans",Arial,sans-serif;color:var(--ink);background:var(--white);position:relative}
section,header,nav,footer{position:absolute;left:0;width:1200px}
.btn{display:inline-block;background:var(--ink);color:var(--white);font:700 15px "Open Sans",sans-serif;padding:14px 28px;border-radius:3px;letter-spacing:.5px}

/* header */
.site-header{top:0;height:120px;display:flex;align-items:center;justify-content:space-between;padding:0 60px}
.brand{display:flex;align-items:center;gap:14px}
.brand-mark{width:44px;height:44px;background:var(--teal)}
.brand-name{font:700 22px "Open Sans",sans-serif;color:var(--teal-dark);max-width:320px;line-height:1.2}
.contact-top{text-align:right;font-size:17px;line-height:1.7}
.contact-top .phone{font-weight:700;font-size:22px;color:var(--teal-dark)}
.contact-top span svg{vertical-align:-3px;margin-right:6px}

.main-nav{top:120px;height:44px;background:var(--nav);display:flex;padding-left:60px}
.main-nav a{color:var(--white);font:600 13px "Open Sans",sans-serif;padding:0 22px;line-height:44px;letter-spacing:.6px;text-decoration:none}
.main-nav a.active{background:var(--teal)}

/* hero */
.hero{top:164px;height:436px;background:linear-gradient(100deg,#eef1f1 0%,#dfe6e8 45%,#b9c6cc 75%,#8fa2ab 100%)}
.hero .visual{position:absolute;inset:0}
.hero-copy{position:absolute;left:60px;top:70px;width:520px}
.hero-copy h1{font:500 37px/1.3 "Raleway",sans-serif;color:var(--ink)}
.hero-copy .btn{margin-top:34px}
.dots{position:absolute;left:60px;bottom:34px;display:flex;gap:8px}
.dots i{width:12px;height:12px;border-radius:50%;background:var(--white);border:2px solid var(--ink)}
.dots i:first-child{background:var(--ink)}

/* need help */
.need-help{top:600px;height:300px;background:var(--teal);color:var(--white);padding:46px 60px 0}
.need-help h2{font:500 31px/1.3 "Raleway",sans-serif;margin-left:270px;width:700px}
.points{display:flex;gap:40px;margin-top:34px;padding:0 110px}
.point{flex:1;display:flex;gap:12px;font-size:13px;line-height:1.55}
.point svg{flex:none;margin-top:3px}

/* services */
.services{top:900px;height:320px;padding-top:28px}
.section-title{display:flex;align-items:center;justify-content:center;gap:18px;font:700 22px "Open Sans",sans-serif;letter-spacing:1px;color:var(--ink)}
.section-title::before,.section-title::after{content:"";width:320px;height:1px;background:var(--line)}
.cards{display:flex;gap:32px;justify-content:center;margin-top:24px}
.card{width:236px;height:222px;border:1px solid var(--line);border-top:6px solid var(--teal);text-align:center;padding:14px 18px 0;position:relative}
.card .icon{width:46px;height:46px;margin:0 auto 8px;display:block}
.card h3{font:700 13px/1.35 "Open Sans",sans-serif;color:var(--teal-dark);letter-spacing:.5px}
.card p{font-size:11px;line-height:1.5;color:var(--muted);margin-top:6px}
.card a{display:block;font:700 10px "Open Sans",sans-serif;color:var(--teal-dark);margin-top:8px;letter-spacing:.5px}

/* team */
.team{top:1220px;height:480px;background:var(--teal);color:var(--white)}
.team-copy{position:absolute;left:60px;top:40px;width:540px}
.team-copy h2{font:700 22px/1.35 "Open Sans",sans-serif;letter-spacing:.3px}
.team-copy h4{font:700 15px "Open Sans",sans-serif;margin-top:22px}
.team-copy p,.team-copy li{font-size:13px;line-height:1.6}
.team-copy ul{list-style:none;margin-top:6px}
.team-copy li::before{content:"\2022";margin-right:8px}
.team-copy .btn{margin-top:24px;background:var(--white);color:var(--ink)}
.team .visual{position:absolute;right:0;top:50px;width:520px;height:380px;background:linear-gradient(135deg,#d7dde0,#9fb0b7 55%,#5f7079);clip-path:polygon(22% 0,100% 0,100% 100%,0 100%)}

/* signup */
.signup{top:1700px;height:120px;background:var(--band);display:flex;align-items:center;justify-content:center;gap:28px}
.signup h2{font:600 28px "Raleway",sans-serif;color:var(--white);letter-spacing:.5px}
.signup .field{width:240px;height:36px;background:var(--white);border-radius:18px;font-size:12px;color:var(--muted);padding:10px 18px}
.signup .btn{background:var(--teal);border-radius:18px;padding:10px 22px;font-size:12px}

/* map & contact */
.locate{top:1820px;height:420px}
.locate .map{position:absolute;inset:0;background:linear-gradient(160deg,#e9ecea,#dfe5e0 60%,#cfdccf)}
.pin{position:absolute;left:628px;top:30px}
.request{position:absolute;left:0;right:0;bottom:0;height:180px;background:var(--teal)}
.request h3{position:absolute;left:430px;top:16px;font:600 22px "Raleway",sans-serif;color:var(--white);letter-spacing:1px}
.inputs{position:absolute;left:430px;top:56px;display:flex;flex-direction:column;gap:8px}
.inputs div,.message{background:var(--white);font-size:12px;color:var(--muted);padding:8px 12px}
.inputs div{width:330px;height:32px}
.message{position:absolute;left:780px;top:56px;width:330px;height:80px}
.send{position:absolute;left:1040px;top:144px;background:var(--ink);color:var(--white);font:700 12px "Open Sans",sans-serif;padding:6px 18px}
.contact-card{position:absolute;left:80px;top:110px;width:260px;height:280px;background:var(--white);border:1px solid var(--line);box-shadow:0 2px 6px rgba(0,0,0,.15)}
.contact-card h3{background:var(--ink);color:var(--white);font:600 18px "Raleway",sans-serif;text-align:center;padding:14px 0;letter-spacing:1px}
.contact-card .body{padding:14px 16px;font-size:12px;line-height:1.75}
.contact-card strong{display:block;color:var(--teal-dark);font-size:14px;line-height:1.3;margin-bottom:8px}
.contact-card .row{white-space:nowrap}
.contact-card svg{vertical-align:-2px;margin-right:6px}

/* footer */
.site-footer{top:2240px;height:64px;background:var(--footer);color:var(--white);font-size:12px;display:flex;align-items:center;justify-content:space-between;padding:0 60px}
.social{display:flex;gap:8px}
.social i{width:28px;height:28px;background:var(--white);opacity:.9}
</style>
</head>
<body>

<header class="site-header">
  <div class="brand">
    <div class="brand-mark"></div>
    <div class="brand-name">Harborline Ledger Partners &amp; Bookkeeping</div>
  </div>
  <div class="contact-top">
    <div class="phone"><span><svg width="16" height="16" viewBox="0 0 24 24"><path fill="#16907e" d="M6.6 10.8a15 15 0 006.6 6.6l2.2-2.2c.3-.3.7-.4 1-.2 1.1.4 2.300.6 3.6.6.6 0 1 .4 1 1V20c0 .6-.4 1-1 1A17 17 0 013 4c0-.6.4-1 1-1h3.5c.6 0 1 .4 1 1 0 1.3.2 2.5.6 3.6.1.3 0 .7-.2 1z"/></svg></span>860.555.0142</div>
    <div><span><svg width="16" height="16" viewBox="0 0 24 24"><rect x="2" y="5" width="20" height="14" fill="none" stroke="#16907e" stroke-width="2"/><path d="M2 5l10 8 10-8" fill="none" stroke="#16907e" stroke-width="2"/></svg></span>info@harborlineledgerpartners.com</div>
  </div>
</header>

<nav class="main-nav">
  <a class="active">HOME</a><a>ABOUT US</a><a>COMPANY</a><a>OUR SERVICES</a><a>HOW IT WORKS</a><a>RESOURCES</a><a>BLOG</a><a>CONTACT US</a>
</nav>

<section class="hero">
  <div class="visual" role="img" aria-label="Photo of smiling business professionals reviewing accounts together"></div>
  <div class="hero-copy">
    <h1>Specialists in Providing Accounting Support Services to Independent Insurance Agencies</h1>
    <span class="btn">LEARN MORE</span>
  </div>
  <div class="dots"><i></i><i></i><i></i></div>
</section>

<section class="need-help">
  <h2>Need help with your insurance agency's accounting and bookkeeping?</h2>
  <div class="points">
    <div class="point"><svg width="18" height="18" viewBox="0 0 24 24"><path d="M4 12l5 5L20 6" fill="none" stroke="#fff" stroke-width="3"/></svg><p>Put our team of insurance agency bookkeeping professionals to work for you.</p></div>
    <div class="point"><svg width="18" height="18" viewBox="0 0 24 24"><path d="M4 12l5 5L20 6" fill="none" stroke="#fff" stroke-width="3"/></svg><p>Have a streamlined workflow in a controlled office in Northern Connecticut.</p></div>
    <div class="point"><svg width="18" height="18" viewBox="0 0 24 24"><path d="M4 12l5 5L20 6" fill="none" stroke="#fff" stroke-width="3"/></svg><p>Receive monthly statements from accountants with 30 years of agency experience.</p></div>
  </div>
</section>

<section class="services">
  <div class="section-title">SERVICES AVAILABLE</div>
  <div class="cards">
    <div class="card">
      <svg class="icon" viewBox="0 0 54 54"><rect x="8" y="14" width="38" height="26" rx="3" fill="#dff3ef" stroke="#1fb29c" stroke-width="2"/><circle cx="27" cy="27" r="6" fill="#1fb29c"/></svg>
      <h3>RECORD DIRECT COMMISSION</h3>
      <p>Direct bill payments are logged by carrier so commissions match your statements.</p>
      <a>LEARN MORE &#8250;</a>
    </div>
    <div class="card">
      <svg class="icon" viewBox="0 0 54 54"><rect x="10" y="8" width="34" height="38" rx="2" fill="#dff3ef" stroke="#1fb29c" stroke-width="2"/><path d="M16 18h22M16 26h22M16 34h14" stroke="#1fb29c" stroke-width="2"/></svg>
      <h3>RECORD DIRECT COMMISSION</h3>
      <p>Agency bill items are posted and tracked so receivables always stay current.</p>
      <a>LEARN MORE &#8250;</a>
    </div>
    <div class="card">
      <svg class="icon" viewBox="0 0 54 54"><circle cx="27" cy="27" r="18" fill="#dff3ef" stroke="#1fb29c" stroke-width="2"/><path d="M27 27V11A16 16 0 0143 27z" fill="#1fb29c"/></svg>
      <h3>RECORD DIRECT COMMISSION</h3>
      <p>Monthly reports summarize income by line and carrier for a clear picture.</p>
      <a>LEARN MORE &#8250;</a>
    </div>
    <div class="card">
      <svg class="icon" viewBox="0 0 54 54"><rect x="12" y="8" width="30" height="38" rx="2" fill="#dff3ef" stroke="#1fb29c" stroke-width="2"/><path d="M18 28l6 6 12-14" fill="none" stroke="#1fb29c" stroke-width="3"/></svg>
      <h3>RECORD DIRECT COMMISSION</h3>
      <p>Bank and trust accounts are reconciled monthly and kept ready for audit.</p>
      <a>LEARN MORE &#8250;</a>
    </div>
  </div>
</section>

<section class="team">
  <div class="team-copy">
    <h2>EXPERIENCED TEAM OF INSURANCE AGENCY BOOKKEEPING PROFESSIONALS MAINTAINING YOUR BOOKS</h2>
    <h4>Affordable, professional services for less than the cost of an in-house bookkeeper</h4>
    <ul>
      <li>Pay for what you need, when you need it</li>
      <li>No more year end headaches, eliminate the rush for records</li>
      <li>Ongoing updates of financial records and reports</li>
    </ul>
    <h4>Capabilities</h4>
    <ul>
      <li>Services from source bookkeeping to financial analysis</li>
      <li>Specializing in agency management and accounting software systems</li>
      <li>Train and educate bookkeepers, managers, owners</li>
    </ul>
    <span class="btn">LEARN MORE</span>
  </div>
  <div class="visual" role="img" aria-label="Photo of an accounting team meeting around a conference table"></div>
</section>

<section class="signup">
  <h2>SIGN UP FOR OUR EMAIL LIST</h2>
  <div class="field">Enter email address</div>
  <span class="btn">SIGN UP NOW</span>
</section>

<section class="locate">
  <div class="map" role="img" aria-label="Street map showing the office location"></div>
  <svg class="pin" width="28" height="40" viewBox="0 0 28 40"><path d="M14 0a14 14 0 00-14 14c0 10 14 26 14 26s14-16 14-26A14 14 0 0014 0z" fill="#d9443a"/><circle cx="14" cy="14" r="5" fill="#fff"/></svg>
  <div class="request">
    <h3>REQUEST INFO</h3>
    <div class="inputs"><div>Name</div><div>Email Address</div><div>Phone</div></div>
    <div class="message">Message</div>
    <div class="send">SEND</div>
  </div>
  <div class="contact-card">
    <h3>CONTACT US</h3>
    <div class="body">
      <strong>Harborline Ledger Partners &amp; Bookkeeping</strong>
      <div>412 Quarry Mill Road<br>Westford, CT 06109</div>
      <div class="row"><svg width="12" height="12" viewBox="0 0 24 24"><path fill="#16907e" d="M6.6 10.8a15 15 0 006.6 6.6l2.2-2.2c.3-.3.7-.4 1-.2 1.1.4 2.3.6 3.6.6.6 0 1 .4 1 1V20c0 .6-.4 1-1 1A17 17 0 013 4c0-.6.4-1 1-1h3.5c.6 0 1 .4 1 1 0 1.3.2 2.5.6 3.6.1.3 0 .7-.2 1z"/></svg>860.555.0142</div>
      <div class="row"><svg width="12" height="12" viewBox="0 0 24 24"><rect x="3" y="4" width="18" height="16" fill="#16907e"/></svg>877.555.0190</div>
      <div class="row"><svg width="12" height="12" viewBox="0 0 24 24"><rect x="2" y="5" width="20" height="14" fill="none" stroke="#16907e" stroke-width="2"/></svg>info@harborlineledgerpartners.com</div>
    </div>
  </div>
</section>

<footer class="site-footer">
  <span>Copyright &copy; 2016 Harborline Ledger Partners &amp; Bookkeeping. All Rights Reserved.</span>
  <div class="social"><i></i><i></i><i></i></div>
</footer>

</body>
</html>
```